KRWB new business card design

We need a business card design for our established business which is Australia wide however based in Melbourne. We are a young team of Financial Planners who specialize in Insurance and Basic super advice for people like us.

We are people who help our clients get things done in a timely and cost effective manner whilst having a good time and a laugh along the way.

We would like this to have a consistent feel with our new e-brochure which i have attached from a color and font perspective.

Industry/Entity Type

Business

Requirements
Must have
• We do not need specific address details rather just the states we are in:

VIC/NSW/QLD/TAS
Nice to have
• Curved edge to mate the brochure

```html
<!DOCTYPE html>
<html lang="en">
<head>
<meta charset="utf-8">
<title>KRWB business card design</title>
<link rel="stylesheet" href="https://fonts.googleapis.com/css2?family=Arimo:ital,wght@0,400;0,700;1,700&family=PT+Sans&display=swap">
<style>
  :root {
    --stage: #8a5a36;
    --label: #1e1208;
    --ink-black: #111;
    --ink-dark: #333;
    --ink-grey: #6d6e70;
    --leaf-light: #6cc04a;
    --leaf-dark: #00a650;
    --paper: #ffffff;
    --divider: #b8b8b8;
  }
  html, body {
    margin: 0;
    width: 1200px;
    height: 788px;
    overflow: hidden;
  }
  body {
    position: relative;
    background: var(--stage);
    font-family: "Arimo", Arial, sans-serif;
  }
  .view-label {
    position: absolute;
    width: 525px;
    text-align: center;
    font-family: "PT Sans", sans-serif;
    font-size: 22px;
    color: var(--label);
  }
  .card {
    position: absolute;
    width: 525px;
    height: 300px;
    border-radius: 20px;
    overflow: hidden;
  }
  .card--dark {
    background: radial-gradient(ellipse at 45% 30%, #3b3b3b 0%, #1a1a1a 45%, #050505 100%);
    color: var(--paper);
  }
  .card--light { background: var(--paper); color: var(--ink-grey); }
  .card--mesh {
    background: radial-gradient(ellipse at 30% 45%, #2c2c2c 0%, #141414 55%, #070707 100%);
    color: var(--paper);
  }

  .brand {
    position: absolute;
    display: flex;
    align-items: center;
    gap: 12px;
    font-weight: 700;
    letter-spacing: 1px;
  }
  .brand__mark { display: block; }

  /* Front */
  .front .brand { left: 0; right: 0; top: 70px; justify-content: center; font-size: 46px; color: var(--leaf-light); }
  .front .brand__mark { width: 30px; height: 30px; background: var(--leaf-light); }
  .name-band {
    position: absolute; left: 0; top: 166px; width: 449px; height: 34px;
    background: var(--leaf-light);
    font-weight: 700; font-size: 18px; line-height: 34px;
    padding-left: 23px; box-sizing: border-box; white-space: nowrap;
  }
  .name-band small { font-size: 14px; }
  .name-band__tab {
    position: absolute; left: 457px; top: 166px; width: 68px; height: 34px;
    background: var(--leaf-dark);
  }
  .contact-list {
    position: absolute; left: 46px; top: 208px; margin: 0; padding: 0; list-style: none;
    font-size: 14px; line-height: 18px;
  }
  .contact-list li { display: flex; align-items: center; gap: 6px; }
  .contact-list svg { width: 11px; height: 11px; fill: var(--paper); }
  .web-area {
    position: absolute; right: 76px; top: 240px; text-align: right;
    font-size: 13px; line-height: 21px;
  }

  /* Specialties */
  .specialties { position: absolute; margin: 0; padding: 0; list-style: none; font-weight: 700; font-size: 14px; }
  .specialties__title { font-style: italic; font-size: 18px; margin-bottom: 12px; }
  .specialties li { height: 34px; }
  .specialties li::before { content: "▪ "; }

  .back-1 .brand { left: 60px; top: 120px; font-size: 42px; color: var(--leaf-light); }
  .back-1 .brand__mark { width: 28px; height: 28px; background: var(--leaf-dark); }
  .back-1 .divider {
    position: absolute; left: 260px; top: 20px; width: 2px; height: 232px;
    background: linear-gradient(to bottom, transparent, var(--divider) 50%, transparent);
  }
  .back-1 .specialties { left: 319px; top: 44px; color: var(--ink-grey); }
  .tagline-band {
    position: absolute; left: 0; bottom: 0; width: 100%; height: 39px;
    background: var(--leaf-light); color: var(--paper);
    text-align: center; font-weight: 700; font-size: 14px; line-height: 39px;
  }

  .back-2 .faint-panel {
    position: absolute; left: 150px; top: 15px; width: 225px; height: 270px;
    border-radius: 24px; background: #f2f6f0;
  }
  .back-2 .specialties { left: 0; right: 0; top: 46px; text-align: center; color: var(--ink-dark); }
  .back-2 .tagline {
    position: absolute; left: 0; right: 0; top: 268px; text-align: center;
    font-weight: 700; font-size: 14px; color: var(--ink-dark);
  }

  .back-3 .brand { left: 62px; top: 118px; font-size: 48px; color: var(--leaf-light); }
  .back-3 .brand__mark { width: 32px; height: 32px; background: var(--leaf-dark); }
  .back-3 .specialties { left: 313px; top: 24px; }
  .back-3 .tagline {
    position: absolute; left: 313px; top: 252px; font-weight: 700; font-size: 14px;
    line-height: 18px; color: var(--leaf-light);
  }
</style>
</head>
<body>
  <div class="view-label" style="left:54px;top:32px">Front</div>
  <div class="view-label" style="left:622px;top:32px">Back - 1</div>
  <div class="view-label" style="left:54px;top:403px">Back - 2</div>
  <div class="view-label" style="left:622px;top:403px">Back - 3</div>

  <section class="card card--dark front" style="left:54px;top:74px">
    <div class="brand"><span class="brand__mark"></span>KRWB</div>
    <div class="name-band">Daniel Harlow, <small>ADFS, BBus, LRS© - Financial Adviser</small></div>
    <div class="name-band__tab"></div>
    <ul class="contact-list">
      <li><svg viewBox="0 0 12 12"><path d="M2 1h3l1 3-2 1a7 7 0 0 0 3 3l1-2 3 1v3a1 1 0 0 1-1 1A10 10 0 0 1 1 2a1 1 0 0 1 1-1z"/></svg>1300 555 014</li>
      <li><svg viewBox="0 0 12 12"><rect x="1" y="4" width="10" height="6" rx="1"/><rect x="3" y="1" width="6" height="3"/></svg>03 9555 0142</li>
      <li><svg viewBox="0 0 12 12"><rect x="3" y="0.5" width="6" height="11" rx="1.2"/></svg>0400 555 218</li>
      <li><svg viewBox="0 0 12 12"><path d="M0 2h12v8H0z M1 3l5 4 5-4" fill="none" stroke="#fff" stroke-width="1.2"/></svg>daniel@krwb.com.au</li>
    </ul>
    <div class="web-area">www.krwb.com.au<br>VIC/NSW/QLD/TAS</div>
  </section>

  <section class="card card--light back-1" style="left:622px;top:74px">
    <div class="brand"><span class="brand__mark"></span>KRWB</div>
    <div class="divider"></div>
    <ul class="specialties">
      <li class="specialties__title" style="height:auto">Specialising in</li>
      <li>Risk Insurance</li>
      <li>Debt Management</li>
      <li>Superannuation</li>
      <li>Wealth Creation</li>
      <li>Retirement Planning</li>
    </ul>
    <div class="tagline-band">SECURE FUTURE, ENHANCED LIFESTYLE</div>
  </section>

  <section class="card card--light back-2" style="left:54px;top:446px">
    <div class="faint-panel"></div>
    <ul class="specialties">
      <li class="specialties__title" style="height:auto">Specialising in</li>
      <li>Risk Insurance</li>
      <li>Debt Management</li>
      <li>Superannuation</li>
      <li>Wealth Creation</li>
      <li>Retirement Planning</li>
    </ul>
    <div class="tagline">SECURE FUTURE, ENHANCED LIFESTYLE</div>
  </section>

  <section class="card card--mesh back-3" style="left:622px;top:446px">
    <div class="brand"><span class="brand__mark"></span>KRWB</div>
    <ul class="specialties">
      <li class="specialties__title" style="height:auto">Specialising in</li>
      <li>Risk Insurance</li>
      <li>Debt Management</li>
      <li>Superannuation</li>
      <li>Wealth Creation</li>
      <li>Retirement Planning</li>
    </ul>
    <div class="tagline">SECURE FUTURE<br>ENHANCED LIFESTYLE</div>
  </section>
</body>
</html>
```